Independent theatre company and venue needs funky web design

Web design for theatre company based in Brisbane Australia. Innovative, grassroots theatre space needs to promote shows in quirky industrial venue. Design needs to be funky, arty but website feels solid and business savvy as well. We need a portal for selling tickets online.
Kettle and Drum is the production company behind this project. We also create theatre in fresh, intimate and humanistic ways.
Target Market(s)
ages 20s-80s
Interested in the arts and fresh, quirky local experiences
Industry/Entity Type
It Company
Coding
Coded - Design and coding required
Number of Pages Required
4 page
Requirements
Must have
- Pages:
- Performances (What's on)
- Hire the Venue (info and enquiry form)
- About Kettle and Drum (history and profile)
- Buy Tickets (patrons can purchase tickets to the shows on at the venue)
- Contact Us/Subscribe
Nice to have
- http://www.tinmill77stage.com/
- Similar in content to this one
- Ideally a website I can update shows (so wordpress or similar user friendly)

```html
<!DOCTYPE html>
<html lang="en">
<head>
<meta charset="utf-8">
<title>Kettle and Drum – Performances</title>
<link href="https://fonts.googleapis.com/css2?family=Open+Sans:wght@400;600&family=Lobster&family=Exo+2:wght@300;400&display=swap" rel="stylesheet">
<style>
:root{
  --ink:#000;
  --white:#fff;
  --nav-active:#ececec;
  --text:#222;
  --muted:#9a9a9a;
  --rule:#d4d4d4;
  --curtain-a:#d2d2d2;
  --curtain-b:#e6e6e6;
  --curtain-c:#c8c8c8;
  --caption-date:#b5b5b5;
}
*{box-sizing:border-box;margin:0;padding:0}
html,body{width:1200px;height:1130px;overflow:hidden;background:var(--white)}
body{position:relative;font-family:"Open Sans",sans-serif;color:var(--text)}
h1,h2,h3{font-weight:400}

.site-header{position:absolute;top:0;left:0;width:1200px;height:104px;border-top:1px solid var(--rule)}
.header-email{position:absolute;left:162px;top:41px;display:flex;align-items:center;gap:12px;font-size:12px;color:var(--text);text-decoration:underline}
.brand{position:absolute;left:0;right:0;top:30px;text-align:center;font-family:"Lobster",cursive;font-size:34px;line-height:40px;color:var(--ink)}
.social{display:flex;gap:10px}
.header-social{position:absolute;left:974px;top:43px}
.social span{display:block;width:15px;height:15px;border-radius:50%;background:var(--ink)}

.main-nav{position:absolute;top:104px;left:0;width:1200px;height:38px;background:var(--ink);display:flex;padding-left:283px}
.main-nav a{display:flex;align-items:center;padding:0 19px;font-size:12px;color:var(--white);text-decoration:none;border-right:1px solid #2e2e2e;white-space:nowrap}
.main-nav a.is-active{background:var(--nav-active);color:var(--ink)}
.main-nav a:last-child{border-right:none}

.shows{position:absolute;top:142px;left:0;width:1200px;height:760px;
  background:repeating-linear-gradient(90deg,var(--curtain-a) 0,var(--curtain-b) 22px,var(--curtain-c) 38px,var(--curtain-b) 56px,var(--curtain-a) 70px)}
.show{position:absolute;width:194px;height:208px;background:var(--ink);overflow:hidden}
.show-photo{height:157px}
.show-info{padding:9px 12px 0}
.show-date{font-size:11px;line-height:14px;color:var(--caption-date)}
.show-title{font-family:"Exo 2",sans-serif;font-weight:400;font-size:14px;line-height:18px;color:var(--white);margin-top:3px;white-space:nowrap}

.feature{position:absolute;left:161px;top:40px;width:422px;height:439px;background:var(--ink);overflow:hidden}
.feature-photo{height:382px;background:radial-gradient(ellipse at 45% 45%,#c8403a 0,#6a1e40 30%,#0c0c2a 60%,#0a2a80 100%)}
.feature-title{height:57px;display:flex;align-items:center;justify-content:center;text-align:center;white-space:nowrap;font-family:"Exo 2",sans-serif;font-weight:400;font-size:25px;line-height:30px;color:var(--white)}

.photo-lounge{background:linear-gradient(180deg,#5a3a26 0%,#9c7b62 45%,#d8ccbe 75%,#8a6a58 100%)}
.photo-portrait{background:radial-gradient(circle at 45% 40%,#c9b48a 0,#7a5a2a 35%,#2a1e0e 75%)}
.photo-stage{background:linear-gradient(180deg,#3a1410 0%,#b8402c 40%,#6a2218 75%,#1e1010 100%)}
.photo-chair{background:radial-gradient(circle at 55% 35%,#d0ccc6 0,#6a6a68 35%,#2a2a2a 80%)}

.site-footer{position:absolute;top:902px;left:0;width:1200px;height:195px;background:var(--white)}
.footer-heading{font-family:"Lobster",cursive;font-size:20px;line-height:26px;color:var(--ink)}
.footer-about{position:absolute;left:162px;top:34px}
.footer-about address{font-style:normal;font-size:12px;line-height:14px;margin-top:12px;color:#333}
.footer-about .hours{font-size:11px;line-height:13px;margin-top:12px;color:#333}
.footer-divider{position:absolute;top:38px;width:1px;height:116px;background:var(--rule)}
.footer-find{position:absolute;left:460px;top:34px}
.footer-find .social{margin-top:14px;margin-left:8px}
.footer-news{position:absolute;left:669px;top:34px}
.news-fields{display:flex;gap:16px;margin-top:12px}
.news-fields input{width:177px;height:33px;border:1px solid #d8d8d8;padding:0 9px;font:10px "Open Sans",sans-serif;color:#444}
.news-fields input::placeholder{color:#444}
.news-submit{margin-top:19px;width:79px;height:29px;background:var(--ink);color:var(--white);border:none;font:12px "Open Sans",sans-serif}

.legal{position:absolute;top:1097px;left:0;width:1200px;height:33px;background:#111;display:flex;align-items:center;justify-content:center;gap:18px;font-size:9px;color:var(--muted);white-space:nowrap}
.legal a{color:var(--muted)}
</style>
</head>
<body>

<header class="site-header">
  <a class="header-email" href="#">
    <svg width="18" height="12" viewBox="0 0 18 12" aria-hidden="true"><rect x="0.5" y="0.5" width="17" height="11" fill="none" stroke="#222"/><path d="M0.5 0.5 L9 7 L17.5 0.5 M0.5 11.5 L6.5 5.5 M17.5 11.5 L11.5 5.5" fill="none" stroke="#222"/></svg>
    info@kettleanddrum.com
  </a>
  <div class="brand">Kettle and Drum</div>
  <div class="social header-social"><span></span><span></span><span></span></div>
</header>

<nav class="main-nav">
  <a href="#" class="is-active">PERFORMANCES</a>
  <a href="#">HIRE THE VENUE</a>
  <a href="#">ABOUT KETTLE AND DRUM</a>
  <a href="#">BUY TICKETS</a>
  <a href="#">CONTACT US</a>
</nav>

<main class="shows">
  <article class="feature">
    <div class="feature-photo" role="img" aria-label="Dancers performing on a dark stage under blue and red light"></div>
    <h1 class="feature-title">Transforming Is Just The Beginning</h1>
  </article>

  <article class="show" style="left:618px;top:40px">
    <div class="show-photo photo-lounge" role="img" aria-label="Actor reclining on a white chaise on stage"></div>
    <div class="show-info"><p class="show-date">19 JAN - 6 FEB</p><h2 class="show-title">Lorem ipsum dolor sit amet</h2></div>
  </article>
  <article class="show" style="left:846px;top:40px">
    <div class="show-photo photo-portrait" role="img" aria-label="Sepia portrait of a performer against foliage"></div>
    <div class="show-info"><p class="show-date">19 JAN - 6 FEB</p><h2 class="show-title">Lorem ipsum dolor sit amet</h2></div>
  </article>
  <article class="show" style="left:618px;top:272px">
    <div class="show-photo photo-stage" role="img" aria-label="Performer kneeling on a red-lit scaffold set"></div>
    <div class="show-info"><p class="show-date">19 JAN - 6 FEB</p><h2 class="show-title">Lorem ipsum dolor sit amet</h2></div>
  </article>
  <article class="show" style="left:846px;top:272px">
    <div class="show-photo photo-chair" role="img" aria-label="Performer seated on a chair in a smoky grey space"></div>
    <div class="show-info"><p class="show-date">19 JAN - 6 FEB</p><h2 class="show-title">Lorem ipsum dolor sit amet</h2></div>
  </article>

  <article class="show" style="left:161px;top:503px">
    <div class="show-photo photo-stage" role="img" aria-label="Performer kneeling on a red-lit scaffold set"></div>
    <div class="show-info"><p class="show-date">19 JAN - 6 FEB</p><h2 class="show-title">Lorem ipsum dolor sit amet</h2></div>
  </article>
  <article class="show" style="left:389px;top:503px">
    <div class="show-photo photo-chair" role="img" aria-label="Performer seated on a chair in a smoky grey space"></div>
    <div class="show-info"><p class="show-date">19 JAN - 6 FEB</p><h2 class="show-title">Lorem ipsum dolor sit amet</h2></div>
  </article>
  <article class="show" style="left:617px;top:503px">
    <div class="show-photo photo-lounge" role="img" aria-label="Actor reclining on a white chaise on stage"></div>
    <div class="show-info"><p class="show-date">19 JAN - 6 FEB</p><h2 class="show-title">Lorem ipsum dolor sit amet</h2></div>
  </article>
  <article class="show" style="left:844px;top:503px">
    <div class="show-photo photo-portrait" role="img" aria-label="Sepia portrait of a performer against foliage"></div>
    <div class="show-info"><p class="show-date">19 JAN - 6 FEB</p><h2 class="show-title">Lorem ipsum dolor sit amet</h2></div>
  </article>
</main>

<footer class="site-footer">
  <section class="footer-about">
    <h3 class="footer-heading">Kettle And Drum</h3>
    <address>12 Foundry Lane<br>Westbury QLD 4101</address>
    <p class="hours">Open during show seasons only :<br>Tuesday – Saturday 8pm</p>
  </section>
  <div class="footer-divider" style="left:405px"></div>
  <section class="footer-find">
    <h3 class="footer-heading">Find Us On</h3>
    <div class="social"><span></span><span></span><span></span></div>
  </section>
  <div class="footer-divider" style="left:607px"></div>
  <section class="footer-news">
    <h3 class="footer-heading">Signup For Newsletter</h3>
    <form>
      <div class="news-fields">
        <input type="text" placeholder="Name ...">
        <input type="email" placeholder="Email ...">
      </div>
      <button class="news-submit" type="button">SIGNUP</button>
    </form>
  </section>
</footer>

<div class="legal">
  <span>COPYRIGHT © &nbsp;KETTLE AND DRUM 2015-2016. ALL RIGHT RESERVED.</span>
  <span>|</span>
  <a href="#">TERMS &amp; CONDITIONS</a>
</div>

</body>
</html>
```